Business Card Design Project

Doctor, Pain Management. Need a new business card design with appointment info on the back. New address is 18 Corvell Road, Suite 304, Brisdale, NJ 07391. Right now I believe the rest of the information is staying the same.

```html
<!DOCTYPE html>
<html lang="en">
<head>
<meta charset="utf-8">
<title>Gentle Relief Pain Care – Business Card</title>
<link href="https://fonts.googleapis.com/css2?family=Open+Sans:wght@400;600;700;800&display=swap" rel="stylesheet">
<style>
  :root {
    --bg: #d9d6d2;
    --card-dark: #121212;
    --card-light: #ffffff;
    --accent: #ea5a0c;
    --ink-light: #e6e6e6;
    --ink-dark: #2b2b2b;
    --rule: #555555;
  }
  * { box-sizing: border-box; margin: 0; padding: 0; }
  html, body { width: 1200px; height: 844px; overflow: hidden; }
  body {
    background: var(--bg);
    font-family: "Open Sans", Arial, sans-serif;
    display: flex; align-items: center; justify-content: center; gap: 60px;
  }
  .card {
    width: 520px; height: 297px; position: relative;
    box-shadow: 0 6px 18px rgba(0,0,0,.25);
  }
  /* Front */
  .card-front { background: var(--card-dark); color: var(--ink-light); display: flex; }
  .front-brand {
    width: 215px; display: flex; align-items: center; justify-content: center; gap: 10px;
  }
  .brand-dot { width: 16px; height: 16px; border-radius: 50%; background: var(--accent); }
  .brand-mark { font-size: 52px; font-weight: 800; color: #f2f2f2; letter-spacing: 1px; }
  .front-divider { width: 1px; background: var(--rule); margin: 62px 0 70px; }
  .front-details { padding: 60px 0 0 20px; font-size: 13px; line-height: 1.45; }
  .doctor-name { color: var(--accent); font-weight: 700; font-size: 15.5px; letter-spacing: .3px; }
  .doctor-title { margin-bottom: 4px; }
  .contact-list { list-style: none; }
  .contact-list li { display: flex; align-items: center; gap: 6px; }
  .contact-list svg { width: 11px; height: 11px; flex: none; }
  .address { padding-left: 17px; }
  /* Back */
  .card-back { background: var(--card-light); color: var(--ink-dark); padding: 26px 34px 0; }
  .back-brand { text-align: center; }
  .back-brand .brand-row { display: flex; align-items: center; justify-content: center; gap: 7px; }
  .back-brand .brand-dot { width: 10px; height: 10px; }
  .back-brand .brand-mark { font-size: 26px; color: var(--ink-dark); }
  .practice-name { font-size: 15px; margin-top: 2px; }
  .form-line { display: flex; align-items: flex-end; font-size: 14px; margin-top: 14px; }
  .dots { flex: 1; border-bottom: 2px dotted #777; margin: 0 6px 4px; }
  .form-line .gap { width: 16px; }
  .days { display: flex; gap: 14px; margin-top: 18px; font-size: 12.5px; }
  .day { display: flex; align-items: center; gap: 4px; }
  .box { width: 15px; height: 15px; border: 1.3px solid #444; }
  .note { font-size: 10.5px; font-weight: 600; margin-top: 18px; text-align: center; }
</style>
</head>
<body>
  <section class="card card-front">
    <div class="front-brand">
      <span class="brand-dot"></span>
      <span class="brand-mark">GRP</span>
    </div>
    <div class="front-divider"></div>
    <div class="front-details">
      <p class="doctor-name">DR. LIANMEI ZHAO, M.D., PH.D.</p>
      <p class="doctor-title">Board Certified Anesthiologist</p>
      <ul class="contact-list">
        <li><svg viewBox="0 0 12 12"><path fill="#ea5a0c" d="M2 1h2.5l1 3-1.5 1a7 7 0 0 0 3 3l1-1.5 3 1V10a1 1 0 0 1-1 1A10 10 0 0 1 1 2a1 1 0 0 1 1-1z"/></svg>973.555.0148</li>
        <li><svg viewBox="0 0 12 12"><rect x="3" y="1" width="6" height="3" fill="#ea5a0c"/><rect x="1" y="4" width="10" height="5" rx="1" fill="#ea5a0c"/><rect x="3" y="7" width="6" height="4" fill="#fff"/></svg>973.555.0162</li>
        <li><svg viewBox="0 0 12 12"><circle cx="6" cy="6" r="5" fill="#ea5a0c"/><path d="M1 6h10M6 1c-2 3-2 7 0 10M6 1c2 3 2 7 0 10" stroke="#121212" fill="none" stroke-width=".8"/></svg>www.gentlereliefpc.com</li>
        <li><svg viewBox="0 0 12 12"><rect x="1" y="2.5" width="10" height="7" fill="#ea5a0c"/><path d="M1 2.5l5 4 5-4" stroke="#121212" fill="none" stroke-width=".9"/></svg>relief.frontdesk@mailbox.com</li>
        <li class="address">18 Corvell Road, Suite 304<br>Brisdale, NJ 07391</li>
      </ul>
    </div>
  </section>

  <section class="card card-back">
    <div class="back-brand">
      <div class="brand-row"><span class="brand-dot"></span><span class="brand-mark">GRP</span></div>
      <p class="practice-name">Gentle Relief Pain Care</p>
    </div>
    <div class="form-line">For :<span class="dots"></span></div>
    <div class="form-line">Date :<span class="dots"></span><span class="gap"></span>Time :<span class="dots"></span>AM / PM</div>
    <div class="days">
      <span class="day"><span class="box"></span>MON</span>
      <span class="day"><span class="box"></span>TUE</span>
      <span class="day"><span class="box"></span>WED</span>
      <span class="day"><span class="box"></span>THU</span>
      <span class="day"><span class="box"></span>FRI</span>
      <span class="day"><span class="box"></span>SAT</span>
    </div>
    <p class="note">If unable to keep your appointment, please contact us as soon as possible</p>
  </section>
</body>
</html>
```